Maplecrest Disability - Social Security Disability Attorneys

Our company is expanding to attract clients nationwide for our social security disability practice. We have a logo, but I am looking for a creative and elegant letterhead that projects an image of being technologically advanced but still professional enough for the legal field. I am looking for the "wow factor" combined with this is still professional enough for a law practice.

Requesting letterhead and business card design
Updates

Had to update and change the logo. The previous logo had a typo. Please send updates with the new logo for consideration. The letterhead and business cards should be professional enough to be used for a law firm. Thanks.

Industry/Entity Type

Law Practice, Law Firm, Healthcare Industry, Government

Colors

Designer to choose colors to be used in the design.

Requirements
Nice to have
• **Please create a vertical design for the business card**

```html
<!DOCTYPE html>
<html lang="en">
<head>
<meta charset="UTF-8">
<title>Maplecrest Disability – Letterhead</title>
<link href="https://fonts.googleapis.com/css2?family=Open+Sans:wght@400;600;700&display=swap" rel="stylesheet">
<style>
  :root {
    --backdrop: #dcdfe0;
    --paper: #ffffff;
    --sky: #5bc0ea;
    --blue: #1a93dd;
    --deep-blue: #0f6fc4;
    --teal: #1a8c8a;
    --orange: #f7861c;
    --brand-blue: #2440a8;
    --ink-grey: #6b6b6b;
  }
  * { margin: 0; padding: 0; box-sizing: border-box; }
  html, body {
    width: 1200px;
    height: 784px;
    overflow: hidden;
    background: var(--backdrop);
    font-family: "Open Sans", Arial, sans-serif;
  }
  .letterhead {
    position: absolute;
    left: 314px;
    top: 22px;
    width: 572px;
    height: 740px;
    background: var(--paper);
    box-shadow: 0 6px 18px rgba(0, 0, 0, 0.18);
    overflow: hidden;
  }
  .edge-bands {
    position: absolute;
    left: 0;
    top: 0;
    width: 90px;
    height: 740px;
  }
  .brand {
    position: absolute;
    left: 62px;
    top: 58px;
    display: flex;
    align-items: center;
    gap: 10px;
  }
  .brand-name {
    font-size: 22px;
    font-weight: 600;
    letter-spacing: 0.08em;
    text-transform: uppercase;
    color: var(--brand-blue);
  }
  .brand-dot {
    width: 14px;
    height: 14px;
    border-radius: 50%;
    background: var(--orange);
  }
  .contact {
    position: absolute;
    left: 82px;
    top: 588px;
    font-size: 14px;
    line-height: 20px;
    font-style: normal;
  }
  .contact-address {
    color: var(--orange);
    font-weight: 700;
  }
  .contact-line {
    color: var(--ink-grey);
    font-weight: 400;
  }
</style>
</head>
<body>
  <main class="letterhead">
    <svg class="edge-bands" viewBox="0 0 90 740" aria-hidden="true">
      <defs>
        <linearGradient id="outerBand" x1="0" y1="0" x2="0" y2="1">
          <stop offset="0" stop-color="#5bc0ea"/>
          <stop offset="0.9" stop-color="#0f6fc4"/>
          <stop offset="1" stop-color="#1a8c8a"/>
        </linearGradient>
        <linearGradient id="innerBand" x1="0" y1="0" x2="0" y2="1">
          <stop offset="0" stop-color="#5bc0ea"/>
          <stop offset="1" stop-color="#1a93dd"/>
        </linearGradient>
      </defs>
      <rect class="band-outer" x="0" y="0" width="9" height="740" fill="url(#outerBand)"/>
      <rect class="band-orange" x="9" y="0" width="10" height="740" fill="#f7861c"/>
      <rect class="band-inner" x="19" y="0" width="9" height="564" fill="url(#innerBand)"/>
      <rect class="band-inner-foot" x="19" y="704" width="9" height="36" fill="#1a8c8a"/>
      <polygon class="contact-tab" points="19,562 56,562 70,576 70,692 54,708 19,708" fill="#f7861c"/>
      <g class="contact-icons" fill="none" stroke="#ffffff" stroke-width="1.4">
        <g class="icon-pin">
          <circle cx="46" cy="598" r="7"/>
          <path d="M46 602 c-2.5 -3 -3.5 -4.5 -3.5 -6 a3.5 3.5 0 0 1 7 0 c0 1.5 -1 3 -3.5 6z" fill="#ffffff" stroke="none"/>
        </g>
        <g class="icon-phone">
          <circle cx="46" cy="638" r="7"/>
          <path d="M43.5 634.5 l1.5 0 l0.8 2 l-1 0.8 a5 5 0 0 0 2.4 2.4 l0.8 -1 l2 0.8 l0 1.5 c-4 0.5 -7 -2.5 -6.5 -6.5z" fill="#ffffff" stroke="none"/>
        </g>
        <g class="icon-mail">
          <circle cx="46" cy="658" r="7"/>
          <rect x="42" y="655" width="8" height="6"/>
          <path d="M42 655 l4 3 l4 -3"/>
        </g>
        <g class="icon-globe">
          <circle cx="46" cy="678" r="7"/>
          <circle cx="46" cy="678" r="4"/>
          <path d="M42 678 h8 M46 674 v8"/>
        </g>
      </g>
    </svg>

    <header class="brand">
      <span class="brand-dot"></span>
      <span class="brand-name">Maplecrest Disability</span>
    </header>

    <address class="contact">
      <div class="contact-address">1250 Harbor Way, Ste 210,</div>
      <div class="contact-address">California, 94110, United States</div>
      <div class="contact-line">(000) 000-0000</div>
      <div class="contact-line">info@maplecrestlaw.com</div>
      <div class="contact-line">www.maplecrestlaw.com</div>
    </address>
  </main>
</body>
</html>
```